Business Card for a mobile physiotherapy company

I need a layout for a business card for a mobile physiotherapy company.
Slogan is "Mobile Physiotherapy - Care That Comes To You"
Phone number is 867-555-0142
Email VardenTherapy@postnest.ca (subject to change with website)
Website www.VardenTherapy.ca
My name and credentials: Luke Varden Luke Varden, BKIN, MSCPT, CGIMS
Information maybe included: Direct Billing, Services including Physiotherapy, IMS, acupuncture
Maybe include facebook and instagram logos
One side with the logo clean and sharp
Other side with details, try not to look too busy, keep everything concise

```html
<!DOCTYPE html>
<html lang="en">
<head>
<meta charset="utf-8">
<title>Varden Therapy – Business Card</title>
<link href="https://fonts.googleapis.com/css2?family=Lato:wght@400;700&family=Tinos:wght@400;700&display=swap" rel="stylesheet">
<style>
  :root {
    --backdrop: #5a5a5a;
    --forest: #0c5148;
    --navy: #2c4873;
    --paper: #ffffff;
    --ink: #444444;
    --rule: #8a8a8a;
  }
  * { margin: 0; padding: 0; box-sizing: border-box; }
  html, body { width: 1200px; height: 802px; overflow: hidden; }
  body { background: var(--backdrop); position: relative; font-family: "Lato", sans-serif; }

  .card {
    position: absolute;
    top: 274px;
    width: 443px;
    height: 265px;
    overflow: hidden;
  }
  .card--details { left: 136px; background: var(--forest); }
  .card--brand { left: 624px; background: var(--paper); }

  .card__band { position: absolute; inset: 0; }

  .contact {
    position: absolute;
    right: 18px;
    top: 40px;
    text-align: right;
    color: var(--paper);
  }
  .contact__name {
    font-family: "Tinos", serif;
    font-weight: 700;
    font-size: 16px;
    letter-spacing: 0.2px;
    text-transform: uppercase;
  }
  .contact__creds {
    font-family: "Tinos", serif;
    font-size: 12.5px;
    margin-top: 1px;
  }
  .contact__lines { list-style: none; margin-top: 14px; font-size: 12.5px; line-height: 16px; }
  .contact__lines li { display: flex; justify-content: flex-end; align-items: center; gap: 3px; }
  .contact__lines svg { width: 11px; height: 11px; flex: none; }

  .services {
    position: absolute;
    right: 20px;
    top: 190px;
    list-style: none;
    text-align: right;
    color: var(--paper);
    font-size: 12.5px;
    line-height: 16px;
  }
  .services li::after { content: " \25CF"; font-size: 8px; vertical-align: 1px; }
  .services .split::before { content: "IMS \25CF  "; font-size: 12.5px; }

  .brand-mark {
    position: absolute;
    left: 210px;
    top: 78px;
    width: 22px;
    height: 22px;
    background: var(--navy);
  }
  .brand-name {
    position: absolute;
    left: 0; right: 0;
    top: 126px;
    text-align: center;
    color: var(--forest);
    font-weight: 700;
    font-size: 28px;
    letter-spacing: 3px;
    text-transform: uppercase;
  }
  .slogan {
    position: absolute;
    left: 0; right: 0;
    top: 198px;
    text-align: center;
    color: var(--ink);
    font-size: 11.2px;
    text-transform: uppercase;
  }
  .social {
    position: absolute;
    left: 76px;
    top: 220px;
    width: 291px;
    height: 18px;
    display: flex;
    align-items: center;
    gap: 6px;
  }
  .social__rule { flex: 1; height: 1px; background: var(--rule); }
  .social__dot { width: 18px; height: 18px; border-radius: 50%; background: var(--navy); }
</style>
</head>
<body>
  <section class="card card--details">
    <svg class="card__band" viewBox="0 0 443 265" role="img" aria-label="Mountain and house emblem in navy and white">
      <polygon points="0,0 38,0 315,265 0,265" fill="#2c4873"/>
      <polygon points="0,0 38,0 0,45" fill="#ffffff"/>
      <polygon points="0,190 230,265 0,265" fill="#ffffff"/>
    </svg>

    <div class="contact">
      <h1 class="contact__name">Luke Varden</h1>
      <p class="contact__creds">BKIN, MSCPT, CGIMS</p>
      <ul class="contact__lines">
        <li>867-555-0142
          <svg viewBox="0 0 12 12"><path d="M1 4c0-2 2-3 5-3s5 1 5 3v1H8.5V4h-5v1H1zM3 6h6l1.5 5h-9z" fill="#fff"/></svg>
        </li>
        <li>VardenTherapy@postnest.ca
          <svg viewBox="0 0 12 12"><rect x="0.5" y="2" width="11" height="8" fill="#fff"/><path d="M0.5 2l5.5 4.5L11.5 2" fill="none" stroke="#0c5148" stroke-width="1"/></svg>
        </li>
        <li>www.VardenTherapy.ca
          <svg viewBox="0 0 12 12"><circle cx="6" cy="6" r="5.5" fill="#fff"/><path d="M3 4h3v3H4zM7 7h2v2H7z" fill="#0c5148"/></svg>
        </li>
      </ul>
    </div>

    <ul class="services">
      <li>Direct Billing</li>
      <li>Physiotherapy</li>
      <li class="split">acupuncture</li>
    </ul>
  </section>

  <section class="card card--brand">
    <span class="brand-mark"></span>
    <h2 class="brand-name">Varden Therapy</h2>
    <p class="slogan">Mobile Physiotherapy - Care That Comes To You</p>
    <div class="social">
      <span class="social__rule"></span>
      <span class="social__dot" aria-label="Social profile"></span>
      <span class="social__dot" aria-label="Social profile"></span>
      <span class="social__rule"></span>
    </div>
  </section>
</body>
</html>
```